UI/UX Re-Do for TallyNest - a free to use project management platform for desktop and mobile.

UI/UX Re-Do for TallyNest
TallyNest is a free to use project management platform for desktop and mobile.
We are looking for help with our UI/UX re-design.
As of now the platform is totally functional.
The problem is around flow and look. We want TN to become something that any one can use to manage and even socialize any project. A project can be something work related like organizing a team around a software build, marketing campaign, shared client file space, etc... In fact, most of our current members are using TN for just such work projects.
We also see a project as planning a wedding, organizing a group trip, a simple to-do list, organizing a kids sports team, and so on...
To become a platform that people will use in their work and personal life we first need to become more intuitive and friendly - while maintaining advanced functionality for more advanced needs.
We need help to beautify, streamline, and simplify - while keeping all the functions.
The quickest way to understand TN, and our current issues is this short video:
https://vidlumo.example/w/Qa7KdP2mXzR
For sure see this link for the entire most recent description AND images:
https://tallynestapp.example/?p=HumbZ4KcWrT
The best way to understand TN is to actually use it:
https://tallynestapp.example
Should you choose to take a run at improving TN here are the details:
Please focus your ideas for mobile, it's where we have the biggest issues.
Feel free to get outside the box.
Avoid swipe oriented designs.
Feel free to focus on ideas over polished outputs.
Use any tool you like, PS, hand drawing, written description if you think that works best.
(FYI - we use mostly use Orvane Slides docs internally)
Point is illustration of ideas over tool choice.
Feel free to:
Create something totally new
And/or riff on what we have now
And/or riff on the new design we are considering (see images below)
|||
If we go the direction of the images/designs below the idea is to give people options on how they see/experience TN.
Just below is what we are calling Ground View. This is a more basic and simple flow. Probably a default to keep new users feeling comfortable at the start.
<img src="https://i.picbarn.example/8wNtLQe.jpg" style="width: 100%;">
https://i.picbarn.example/8wNtLQe.jpg
|||
We are calling this optional view Sky View. It is more advanced and can show all project, goal(renamed 'milestones') at the same time. This is more of a paint job on the current design.
<img src="https://i.picbarn.example/vhRmJxd.jpg" style="width: 100%;">
https://i.picbarn.example/vhRmJxd.jpg
|||
If you're submitting please let us know if you can also do the PS files for dev.
Not required, but once we nail down the concepts we want someone to hone in the PS files.
As an optional bonus we will also be giving credit to you/your company in TN.
Let us know if you do or don't want that.
We are excited to see your work!!
<img src=" " style="width: 100%;">
Target Market(s)
Anyone who needs to organize any project, big or small. The key is to make a super friendly user experience for new users while retaining advanced functions.
Industry/Entity Type
Management
Number of Pages Required
2 page

```html
<!DOCTYPE html>
<html lang="en">
<head>
<meta charset="utf-8">
<title>TallyNest Dashboard</title>
<link href="https://fonts.googleapis.com/css2?family=Open+Sans:wght@400;600;700&display=swap" rel="stylesheet">
<style>
:root{
  --navy:#234a66;
  --brand:#f0932b;
  --nav-muted:#8fb4d3;
  --ink:#1c1c1c;
  --muted:#555;
  --faint:#a9a9a9;
  --line:#e6e6e6;
  --panel:#efefef;
  --blue:#3f82dc;
  --grey-btn:#b0b0b0;
  --green:#57c38e;
  --dot-green:#3fc37a;
  --alert:#e9534f;
}
*{box-sizing:border-box;margin:0;padding:0}
html,body{width:1200px;height:675px;overflow:hidden;background:#fff;font-family:"Open Sans",Arial,sans-serif;color:var(--ink)}
.app{position:relative;width:1200px;height:675px;overflow:hidden}

.topbar{position:absolute;left:0;top:0;width:1200px;height:50px;background:var(--navy)}
.brand{position:absolute;left:27px;top:14px;font-size:16px;font-weight:700;color:var(--brand);letter-spacing:.2px}
.main-nav{position:absolute;top:19px;left:461px;display:flex;gap:23px;font-size:8.5px;font-weight:600;letter-spacing:.3px}
.main-nav a{color:var(--nav-muted);text-decoration:none}
.main-nav a.active{color:#fff;font-weight:700}
.icon-search{position:absolute;left:1107px;top:17px}
.icon-bell{position:absolute;left:1149px;top:17px}
.badge{position:absolute;left:1157px;top:14px;width:13px;height:13px;border-radius:50%;background:var(--alert);color:#fff;font-size:8px;line-height:13px;text-align:center}

.pagebar{position:absolute;left:0;top:50px;width:1200px;height:63px;border-bottom:1px solid var(--line);background:#fff}
.page-title{position:absolute;left:27px;top:21px;font-size:15px;font-weight:700;letter-spacing:.2px}
.stat{position:absolute;top:16px;text-align:center;line-height:1}
.stat b{display:block;font-size:18px;font-weight:700}
.stat span{display:block;font-size:11.5px;color:var(--muted);margin-top:1px}
.menu-icon{position:absolute;left:1159px;top:26px}

.filters{position:absolute;left:28px;top:125px;width:231px}
.filter{display:block;height:37.6px;margin-bottom:12.8px;padding-left:10px;line-height:37.6px;font-size:9px;font-weight:700;color:#fff;background:var(--blue);border:1px solid #3574c8}
.filter.current{background:var(--grey-btn);border-color:#a3a3a3}

.board{position:absolute;left:278px;top:113px;width:250px;height:562px;background:#fff}
.col-head{position:relative;height:37px;background:var(--panel);font-size:8.5px;font-weight:700;letter-spacing:.2px;line-height:37px;padding-left:38px}
.col-head .toggle{position:absolute;left:18px;top:0;color:var(--faint);font-weight:400;font-size:11px}
.col-head .more{position:absolute;right:24px;top:0;color:var(--faint);font-size:10px;letter-spacing:0}
.col-head .status{position:absolute;right:5px;top:6px;width:4px;height:4px;border-radius:50%;background:var(--dot-green)}
.col-head .status.idle{background:#bbb}
.col-body{padding:12px 19px 31px 19px}
.card{height:50px;border:1px solid var(--line);margin-bottom:6.4px;padding:6px 11px;box-shadow:0 1px 1px rgba(0,0,0,.04)}
.card-title{font-size:9px;color:#444}
.card-meta{display:flex;gap:12px;margin-top:13px;font-size:7px;color:var(--faint);align-items:center}
.card-meta span{display:flex;align-items:center;gap:3px}
.add-goal{display:flex;align-items:center;justify-content:center;gap:7px;height:25px;margin-top:12px;background:var(--green);color:#fff;font-size:9px;font-weight:600;border:1px solid #4bb37f}
.col-head.spaced{margin-top:1px}
</style>
</head>
<body>
<div class="app">
  <header class="topbar">
    <div class="brand">TALLYNEST</div>
    <nav class="main-nav">
      <a class="active">DASHBOARD</a>
      <a>MY PROJECTS</a>
      <a>PUBLIC PROJECT</a>
      <a>ADMIN</a>
    </nav>
    <svg class="icon-search" width="16" height="16" viewBox="0 0 16 16" fill="none" stroke="#fff" stroke-width="1.6"><circle cx="9.5" cy="6.5" r="4.8"/><line x1="6" y1="10" x2="1.5" y2="14.5"/></svg>
    <svg class="icon-bell" width="14" height="16" viewBox="0 0 14 16" fill="none" stroke="#fff" stroke-width="1.4"><path d="M2 11.5V7a5 5 0 0 1 10 0v4.5l1.2 1.3H.8z"/><path d="M5.5 14.2a1.6 1.6 0 0 0 3 0"/></svg>
    <div class="badge">5</div>
  </header>

  <section class="pagebar">
    <h1 class="page-title">DASHBOARD</h1>
    <div class="stat" style="left:961px;width:60px"><b>5</b><span>Projects</span></div>
    <div class="stat" style="left:1027px;width:50px"><b>42</b><span>Goal</span></div>
    <div class="stat" style="left:1087px;width:50px"><b>76</b><span>Task</span></div>
    <svg class="menu-icon" width="14" height="11" viewBox="0 0 14 11" fill="#234a66"><rect width="14" height="2"/><rect y="4.5" width="14" height="2"/><rect y="9" width="14" height="2"/></svg>
  </section>

  <aside class="filters">
    <a class="filter current">All Projects</a>
    <a class="filter">TallyNest Top Project Picks</a>
    <a class="filter">Most Popular Public Projects</a>
    <a class="filter">All Public Projects</a>
  </aside>

  <main class="board">
    <div class="col-head"><span class="toggle">—</span>STARTUP STARTER KITS<span class="more">⋮</span><i class="status"></i></div>
    <div class="col-body">
      <div class="card"><div class="card-title">Meeting Notes / Business SCRUM</div><div class="card-meta"><span><svg width="9" height="7" viewBox="0 0 9 7" fill="#b5b5b5"><path d="M0 0h9v5H2L0 7z"/></svg>7</span><span><svg width="8" height="8" viewBox="0 0 8 8" fill="none" stroke="#b5b5b5" stroke-width="1"><path d="M6.5 3.5 3.5 6.5a1.6 1.6 0 0 1-2.3-2.3L4.6.9a1 1 0 0 1 1.5 1.5L3 5.4"/></svg>5</span></div></div>
      <div class="card"><div class="card-title">Meeting Notes / Business SCRUM</div><div class="card-meta"><span><svg width="9" height="7" viewBox="0 0 9 7" fill="#b5b5b5"><path d="M0 0h9v5H2L0 7z"/></svg>7</span></div></div>
      <div class="card"><div class="card-title">Fund Raising / Corp Dev</div><div class="card-meta"><span><svg width="9" height="7" viewBox="0 0 9 7" fill="#b5b5b5"><path d="M0 0h9v5H2L0 7z"/></svg>7</span></div></div>
      <div class="card"><div class="card-title">Operating Finance</div><div class="card-meta"><span><svg width="9" height="7" viewBox="0 0 9 7" fill="#b5b5b5"><path d="M0 0h9v5H2L0 7z"/></svg>7</span></div></div>
      <div class="card"><div class="card-title">Sales / Business Development</div><div class="card-meta"><span><svg width="9" height="7" viewBox="0 0 9 7" fill="#b5b5b5"><path d="M0 0h9v5H2L0 7z"/></svg>7</span></div></div>
      <div class="card"><div class="card-title">Marketing</div><div class="card-meta"><span><svg width="9" height="7" viewBox="0 0 9 7" fill="#b5b5b5"><path d="M0 0h9v5H2L0 7z"/></svg>7</span></div></div>
      <div class="card"><div class="card-title">Other</div><div class="card-meta"><span><svg width="9" height="7" viewBox="0 0 9 7" fill="#b5b5b5"><path d="M0 0h9v5H2L0 7z"/></svg>7</span></div></div>
      <div class="add-goal"><svg width="13" height="13" viewBox="0 0 13 13" fill="none" stroke="#fff" stroke-width="1.1"><circle cx="6.5" cy="6.5" r="5.8"/><path d="M6.5 3.5v6M3.5 6.5h6"/></svg>Add New Goal</div>
    </div>
    <div class="col-head"><span class="toggle">+</span>TN PUBLIC PROJECT INFO<span class="more">⋮</span><i class="status idle"></i></div>
    <div class="col-head spaced"><span class="toggle">+</span>TN UI/UX RE-DESIGN CONCEPT<span class="more">⋮</span><i class="status"></i></div>
  </main>
</div>
</body>
</html>
```